High-end construction company needs a business card design

We need a modern looking business card that draws people in, is memorable and looks so good people will want to sick it on their fridges.
On the first side what is needed are:
Logo
My name - Tomasz Brelwik
Title - Managing Director
Website - www.varkelt.co.uk
Email - tomasz@varkelt.co.uk
Telephone - 020 5194 6281
Mobile - 07845139072
On the back side was is needed is a list of all the services we provide:
-Kitchen Renovations
-Bathroom Renovations
-House Renovations
-Garage Conversions
-Extensions
-Loft Conversions
-Conservatories
-Carpentry
-Tiling
-Electrical
-Plumbing & Heating
-Bricklaying
-Landscaping
-Decorating
-Plastering
We would like the colours to be the same shades as on the logo with grey or black for the words.
Target Market(s)
Anyone who needs building work done
Contact Information for Business Card
This business card is for a construction company which strives to deliver excellent service and quality.
The look and feel of the card should represent this.
Requirements
Must have
- On the first side what is needed are:
Logo
My name - Tomasz Brelwik
Title - Managing Director
Website - www.varkelt.co.uk
Email - tomasz@varkelt.co.uk
Telephone - 020 5194 6281
Mobile - 07845139072
Nice to have
- Cool looking features

```html
<!DOCTYPE html>
<html lang="en">
<head>
<meta charset="utf-8">
<title>Varkelt Construction Ltd – Business Card</title>
<link rel="stylesheet" href="https://fonts.googleapis.com/css2?family=Arimo:wght@400;700&family=Archivo+Black&display=swap">
<style>
  :root {
    --backdrop: #2b2b2b;
    --card: #0e0e0e;
    --card-edge: #1c1c1c;
    --green: #6cc540;
    --green-deep: #4c9a3a;
    --text-grey: #d2d2d2;
    --text-muted: #bdbdbd;
    --divider: #3a3a3a;
  }
  * { margin: 0; padding: 0; box-sizing: border-box; }
  html, body {
    width: 1200px; height: 900px; overflow: hidden;
    background: var(--backdrop);
    font-family: "Arimo", Arial, sans-serif;
  }
  .sheet {
    width: 1200px; height: 900px;
    display: flex; flex-direction: column;
    align-items: center; justify-content: center; gap: 36px;
  }
  .card {
    width: 700px; height: 400px;
    background: var(--card);
    border-radius: 26px;
    border: 1px solid var(--card-edge);
    box-shadow: 0 14px 30px rgba(0,0,0,.45);
    position: relative;
    overflow: hidden;
  }

  /* Front */
  .card--front { display: flex; align-items: stretch; }
  .brand {
    width: 360px; flex: none; display: flex; flex-direction: column;
    justify-content: flex-end; padding: 0 24px 72px 50px;
    color: var(--green); font-weight: 700;
  }
  .brand__row { display: flex; align-items: center; gap: 14px; }
  .brand__mark { width: 20px; height: 20px; background: var(--green); flex: none; }
  .brand__name { font-size: 50px; line-height: 1; letter-spacing: 1px; }
  .brand__tagline { font-size: 17px; letter-spacing: 4px; margin-top: 10px; }
  .front__divider {
    width: 1px; flex: none; background: var(--divider); margin: 96px 0 70px;
  }
  .contact { padding: 96px 28px 0 36px; flex: 1; min-width: 0; }
  .contact__name {
    font-family: "Archivo Black", "Arimo", sans-serif;
    color: var(--green); font-size: 23px; text-transform: uppercase; line-height: 1;
    white-space: nowrap;
  }
  .contact__title { color: var(--text-grey); font-size: 18px; margin-top: 6px; }
  .contact__list { list-style: none; margin-top: 34px; }
  .contact__item {
    display: flex; align-items: center; gap: 12px;
    color: var(--text-grey); font-size: 19px; line-height: 30px;
    white-space: nowrap;
  }
  .contact__item--web { color: var(--green); }
  .contact__icon { width: 17px; height: 17px; flex: none; }

  /* Back */
  .card--back {
    display: flex; gap: 46px; padding: 104px 0 0 74px;
  }
  .services { list-style: none; }
  .services__item {
    display: flex; align-items: center; gap: 14px;
    color: var(--text-muted); font-size: 20px; line-height: 31px;
    text-transform: uppercase; letter-spacing: .3px;
    white-space: nowrap;
  }
  .services__item::before {
    content: ""; width: 9px; height: 9px; border-radius: 50%;
    background: var(--green); flex: none;
  }
  .services--secondary { margin-top: -48px; }
</style>
</head>
<body>
<main class="sheet">

  <section class="card card--front" aria-label="Business card front">
    <div class="brand">
      <div class="brand__row">
        <span class="brand__mark"></span>
        <span class="brand__name">VARKELT</span>
      </div>
      <span class="brand__tagline">CONSTRUCTION LTD</span>
    </div>
    <div class="front__divider"></div>
    <div class="contact">
      <h1 class="contact__name">Tomasz Brelwik</h1>
      <p class="contact__title">Managing Director</p>
      <ul class="contact__list">
        <li class="contact__item">
          <svg class="contact__icon" viewBox="0 0 24 24" fill="none" stroke="#6cc540" stroke-width="2.4" stroke-linecap="round" stroke-linejoin="round"><path d="M5 3h4l2 5-2.5 1.5a11 11 0 0 0 6 6L16 13l5 2v4a2 2 0 0 1-2 2A16 16 0 0 1 3 5a2 2 0 0 1 2-2z"/></svg>
          020 5194 6281
        </li>
        <li class="contact__item">
          <svg class="contact__icon" viewBox="0 0 24 24" fill="none" stroke="#6cc540" stroke-width="2.4" stroke-linecap="round"><rect x="6" y="2" width="12" height="20" rx="2"/><line x1="11" y1="18" x2="13" y2="18"/></svg>
          07845139072
        </li>
        <li class="contact__item">
          <svg class="contact__icon" viewBox="0 0 24 24" fill="none" stroke="#6cc540" stroke-width="2.4" stroke-linejoin="round"><rect x="2" y="5" width="20" height="14"/><path d="M2 5l10 8 10-8"/></svg>
          tomasz@varkelt.co.uk
        </li>
        <li class="contact__item contact__item--web">
          <svg class="contact__icon" viewBox="0 0 24 24" fill="none" stroke="#6cc540" stroke-width="2.2"><circle cx="12" cy="12" r="10"/><ellipse cx="12" cy="12" rx="4" ry="10"/><line x1="2" y1="12" x2="22" y2="12"/></svg>
          www.varkelt.co.uk
        </li>
      </ul>
    </div>
  </section>

  <section class="card card--back" aria-label="Business card back">
    <ul class="services services--primary">
      <li class="services__item">Kitchen Renovations</li>
      <li class="services__item">Bathroom Renovations</li>
      <li class="services__item">House Renovations</li>
      <li class="services__item">Garage Conversions</li>
      <li class="services__item">Extensions</li>
      <li class="services__item">Loft Conversions</li>
      <li class="services__item">Conservatories</li>
      <li class="services__item">Carpentry</li>
    </ul>
    <ul class="services services--secondary">
      <li class="services__item">Tiling</li>
      <li class="services__item">Electrical</li>
      <li class="services__item">Plumbing &amp; Heating</li>
      <li class="services__item">Bricklaying</li>
      <li class="services__item">Landscaping</li>
      <li class="services__item">Decorating</li>
      <li class="services__item">Plastering</li>
    </ul>
  </section>

</main>
</body>
</html>
```